New Fitness Company looking for creative website design

I am building a new fitness matching service. To match customers looking for fitness services to professionals that meet their requirements

My business will have 5 different divisions and I would like to have tabs for each division

1. Matching client to trainer - I need to have video upload capability on the site
2. Corporate personal training services

-The site needs a shopping cart as well as payment capability.
- I am looking for the site to be bright and inviting as well as have clients and trainers going through some type of workout on the main page.
- I also need the capability to capture email addresses
- We are going to have a section that ask the customer questions to match up the trainer so that needs to be a part of the site
-Ability to have trainers rated in a 1 star to 5 stars as well as reviews
- Site should be inviting, bright and vibrant colors that catch the eye and is easy to use
- Similar sites for inspiration are www.zavrello.com where you give a description of how the service works, short video and various services.

Target Market(s)

mid income to high income, mix of female and male customers

Industry/Entity Type

Fitness

Coding

Coded - Design and coding required

Number of Pages Required

5+ page

Font styles to use
Serif
Sans Serif

Requirements
Must have
• Must have the logos that I provided in the website
Should not have
• Not looking for bodybuilders on website. This is for everyday people that are interested in staying in shape and working out. So active fit people will resonate with my prospects

```html
<!DOCTYPE html>
<html lang="en">
<head>
<meta charset="utf-8">
<title>Brisko Fitness</title>
<link href="https://fonts.googleapis.com/css2?family=Poiret+One&family=Montserrat:wght@400;600;700&family=Open+Sans:ital,wght@0,400;0,600;0,700;1,400&display=swap" rel="stylesheet">
<style>
:root{
  --orange:#f2a23a;
  --orange-dark:#e8891c;
  --green:#3ba53b;
  --green-light:#e6f3e3;
  --pink:#e0608a;
  --teal:#3bb3c3;
  --blue:#3a86d4;
  --dark:#1f1a15;
  --darker:#181410;
  --text:#555;
  --muted:#888;
  --line:#ddd;
  --white:#fff;
}
*{box-sizing:border-box;margin:0;padding:0}
html,body{width:1200px;height:4712px;overflow:hidden}
body{font-family:"Open Sans",sans-serif;color:var(--text);background:var(--white);position:relative}
section,header,footer{position:absolute;left:0;width:1200px}
.abs{position:absolute}
.title{font-family:"Poiret One",cursive;font-weight:400;color:var(--orange);text-align:center;font-size:40px;letter-spacing:1px}
.photo{position:absolute}

/* hero */
.hero{top:0;height:660px;background:linear-gradient(100deg,#d9d4cf 0%,#ece8e4 35%,#c9b8ad 60%,#5a4a44 100%)}
.nav{top:30px;left:100px;width:1000px;height:80px}
.brand{position:absolute;left:0;top:18px;display:flex;align-items:center;gap:10px;font-family:"Montserrat",sans-serif;font-weight:700;font-size:24px;color:var(--green)}
.brand i{width:22px;height:22px;border-radius:50%;background:var(--orange);display:block}
.menu{position:absolute;left:310px;top:28px;display:flex;gap:38px;font-size:13px;color:#444}
.menu .active{color:var(--green);font-weight:600}
.menu-dot{position:absolute;right:0;top:18px;width:36px;height:36px;border-radius:50%;background:var(--orange)}
.hero-copy{top:340px;left:175px}
.hero-copy h1{font-family:"Montserrat",sans-serif;font-weight:600;font-size:46px;color:var(--white)}
.hero-copy p{font-family:"Montserrat",sans-serif;font-size:21px;color:var(--orange);margin-top:4px}
.arrow{position:absolute;top:340px}

/* welcome */
.welcome{top:660px;height:832px;background:#f7f7f7}
.welcome .lead{position:absolute;top:140px;left:230px;width:740px;text-align:center;font-size:13px;line-height:20px;color:#444}
.welcome .sub{position:absolute;top:242px;width:100%;text-align:center;font-size:15px;color:var(--blue)}
.feature{position:absolute;width:240px;font-size:11.5px;line-height:18px;color:var(--muted)}
.feature h3{font-weight:400;font-size:16px;margin-bottom:6px}
.feature.left{text-align:right}
.ficon{position:absolute;width:56px;height:56px;border-radius:50%;display:flex;align-items:center;justify-content:center}

/* corporate */
.corporate{top:1498px;height:543px;background:var(--dark)}
.card{position:absolute;top:179px;width:242px}
.card .photo{position:relative;height:201px}
.card h4{color:var(--white);font-weight:600;font-size:17px;margin-top:20px}
.card p{color:#ddd;font-size:13px;margin-top:8px}

/* matching */
.matching{top:2057px;height:534px;background:var(--white)}
.matching .title{text-align:left;position:absolute;left:100px;top:60px}
.matching .intro{position:absolute;left:100px;top:118px;width:420px;font-style:italic;font-size:13px;line-height:19px;color:#555}
.step{position:absolute;left:100px;width:428px;height:72px;background:#e8e8e8;display:flex}
.step .play{width:66px;background:var(--green);display:flex;align-items:center;justify-content:center;flex:none}
.step .txt{padding:12px 14px}
.step h4,.caption h4{font-size:15px;font-weight:600;color:#333}
.step p,.caption p{font-size:12px;font-style:italic;color:#666;margin-top:4px}
.caption{position:absolute;left:578px;top:395px;width:521px;height:60px;background:#e8e8e8;display:flex}

/* trainer */
.trainer{top:2594px;height:556px;background:var(--dark)}
.tbox{position:absolute;left:182px;top:188px;width:832px;height:270px;border:2px solid #cfc7bd}
.avatar{position:absolute;left:540px;top:169px;width:120px;height:120px;border-radius:50%;border:3px solid var(--white);background:linear-gradient(#d8b79a,#a87a58)}
.stars{position:absolute;top:318px;width:100%;text-align:center;color:var(--orange);font-size:22px;letter-spacing:3px}
.quote{position:absolute;left:250px;top:365px;width:700px;text-align:center;font-size:12px;line-height:21px;color:#cfc7bd}
.tname{position:absolute;top:446px;width:100%;text-align:center;color:var(--green);font-size:13px;letter-spacing:1px}

/* products & faq */
.shop{top:3150px;height:577px;background:var(--white)}
.shop .title{position:absolute;top:80px;text-align:left}
.product{position:absolute;top:163px;width:205px;height:330px;border:1px solid var(--line);background:var(--white)}
.product .photo{position:relative;height:180px}
.product h5{font-size:12px;font-weight:700;color:#333;margin:12px 10px 0}
.product .desc{font-size:11px;color:#777;margin:2px 10px 0}
.price{display:flex;justify-content:space-between;margin:12px 10px 0;color:var(--orange);font-weight:700;font-size:17px}
.price span{font-size:13px;letter-spacing:1px}
.buy{display:inline-block;margin:10px;background:var(--green);color:var(--white);font-size:11px;font-weight:700;padding:7px 14px}
.faq{position:absolute;left:823px;top:165px;width:285px;font-size:12px;color:#444}
.faq li{list-style:none;display:flex;gap:10px;margin-bottom:19px}
.faq li::before{content:"";width:11px;height:11px;border:1px solid #999;flex:none;margin-top:3px}
.faq .answer{font-size:12px;line-height:19px;color:#555;margin:-4px 0 24px 22px}

/* newsletter */
.newsletter{top:3727px;height:255px;background:var(--green-light)}
.newsletter .title{position:absolute;top:36px;width:100%;color:var(--green);font-size:36px}
.newsletter .sub{position:absolute;top:88px;width:100%;text-align:center;font-family:"Poiret One",cursive;color:var(--orange);font-size:26px}
.nl-input{position:absolute;left:374px;top:162px;width:276px;height:44px;background:var(--white);font-size:11px;color:#aaa;padding:14px 18px}
.nl-btn{position:absolute;left:650px;top:162px;width:179px;height:44px;background:var(--orange-dark);color:var(--white);font-size:17px;text-align:center;line-height:44px}

/* contact */
.contact{top:3988px;height:640px;background:var(--white)}
.contact .intro{position:absolute;top:142px;left:250px;width:700px;text-align:center;font-style:italic;font-size:13px;line-height:22px;color:#666}
.field{position:absolute;border:1px solid var(--line);font-size:11px;color:#aaa;padding:14px 16px}
.info{position:absolute;left:807px;font-size:14px;color:#444;display:flex;align-items:center;gap:22px}
.info svg{width:18px;height:18px}
.send{position:absolute;left:807px;top:509px;width:148px;height:44px;background:var(--orange-dark);color:var(--white);text-align:center;line-height:44px;font-size:18px;font-family:"Poiret One",cursive;font-weight:700}

/* footer */
.footer{top:4628px;height:84px;background:var(--darker)}
.footer .copy{position:absolute;left:100px;top:34px;font-size:12px;color:#666}
.social{position:absolute;left:902px;top:27px;display:flex;gap:10px}
.social i{width:26px;height:26px;display:block}
.footer .page{position:absolute;left:1115px;top:34px;font-size:12px;color:#888}
</style>
</head>
<body>

<header class="hero">
  <div class="photo" role="img" aria-label="Woman in sportswear stretching on the floor of a bright studio" style="left:540px;top:0;width:660px;height:660px;background:linear-gradient(90deg,rgba(210,200,192,0) 0%,#b49a88 40%,#5b4740 100%)"></div>
  <nav class="nav abs">
    <div class="brand"><i></i>Brisko Fitness</div>
    <ul class="menu">
      <li class="active">Home</li><li>About Us</li><li>Classes</li><li>Gallery</li><li>Schedule</li><li>Products</li><li>Contact Us</li>
    </ul>
    <span class="menu-dot"></span>
  </nav>
  <div class="hero-copy abs">
    <h1>Brisko Fitness</h1>
    <p>Is To Make You Happy And Healthy Life</p>
  </div>
  <svg class="arrow" style="left:40px" width="24" height="40" viewBox="0 0 24 40"><path d="M20 2 4 20l16 18" fill="none" stroke="#fff" stroke-width="3"/></svg>
  <svg class="arrow" style="right:40px" width="24" height="40" viewBox="0 0 24 40"><path d="M4 2l16 18L4 38" fill="none" stroke="#fff" stroke-width="3"/></svg>
</header>

<section class="welcome">
  <h2 class="title abs" style="top:78px;width:100%">Welcome to Brisko Fitness</h2>
  <p class="lead">I must explain to you how all this mistaken idea of denouncing pleasure and praising pain was born and I will give you a complete account of the system, and expound the actual teachings of the great explorer of the truth, the master-builder of human happiness</p>
  <p class="sub">Brisko Fitness</p>
  <div class="ficon" style="left:566px;top:292px;background:var(--blue)"><svg width="24" height="24" viewBox="0 0 24 24"><circle cx="12" cy="12" r="9" fill="none" stroke="#fff" stroke-width="2"/><circle cx="12" cy="12" r="3" fill="#fff"/></svg></div>
  <div class="photo" role="img" aria-label="Woman holding a seated yoga pose" style="left:330px;top:375px;width:440px;height:380px;background:radial-gradient(ellipse at 50% 55%,#c8a58c 0%,#e0cfc3 45%,rgba(247,247,247,0) 72%)"></div>

  <div class="feature left" style="left:125px;top:410px"><h3 style="color:var(--pink)">Healthy Daily Use</h3>No one rejects, dislikes, or avoids pleasure itself, because it is pleasure, but because those...</div>
  <div class="ficon" style="left:386px;top:412px;background:var(--pink)"><svg width="24" height="24" viewBox="0 0 24 24"><path d="M12 20 4 12a4.5 4.5 0 0 1 8-5 4.5 4.5 0 0 1 8 5z" fill="none" stroke="#fff" stroke-width="2"/></svg></div>

  <div class="feature left" style="left:60px;top:586px"><h3 style="color:var(--orange)">Meditation practice</h3>At vero eos et accusamus et iusto odio dignissimos ducimus qui blandiitis...</div>
  <div class="ficon" style="left:310px;top:588px;background:var(--orange)"><svg width="24" height="24" viewBox="0 0 24 24"><path d="M12 4v16M6 10h12" stroke="#fff" stroke-width="2"/></svg></div>

  <div class="ficon" style="left:748px;top:412px;background:var(--teal)"><svg width="24" height="24" viewBox="0 0 24 24"><path d="M2 12s4-6 10-6 10 6 10 6-4 6-10 6S2 12 2 12z" fill="none" stroke="#fff" stroke-width="2"/><circle cx="12" cy="12" r="3" fill="#fff"/></svg></div>
  <div class="feature" style="left:830px;top:410px"><h3 style="color:var(--teal)">Yoga Month Challenge</h3>No one rejects, dislikes, or avoids pleasure itself, because it is pleasure, but because those...</div>

  <div class="ficon" style="left:818px;top:588px;background:var(--blue)"><svg width="24" height="24" viewBox="0 0 24 24"><circle cx="8" cy="8" r="3" fill="#fff"/><circle cx="16" cy="8" r="3" fill="#fff"/><circle cx="12" cy="16" r="4" fill="#fff"/></svg></div>
  <div class="feature" style="left:900px;top:586px"><h3 style="color:var(--blue)">Balance Body &amp; Mind</h3>At vero eos et accusamus et iusto odio dignissimos ducimus qui blandiitis...</div>
</section>

<section class="corporate">
  <h2 class="title abs" style="top:74px;width:100%;color:var(--white)">Corporate Personal Training</h2>
  <div class="card" style="left:100px"><div class="photo" role="img" aria-label="Woman training on a gym machine" style="background:linear-gradient(135deg,#8a7a8c,#3f3440)"></div><h4>Molestias Excepturi sint</h4><p>Timing : 17.00Am - 20.00Pm</p></div>
  <div class="card" style="left:352px"><div class="photo" role="img" aria-label="Woman tying running shoes" style="background:linear-gradient(135deg,#b9b3ad,#55504b)"></div><h4>Molestias Excepturi sint</h4><p>Timing : 17.00Am - 20.00Pm</p></div>
  <div class="card" style="left:603px"><div class="photo" role="img" aria-label="Two runners jogging outdoors" style="background:linear-gradient(135deg,#8fc06a,#e05a78)"></div><h4>Molestias Excepturi sint</h4><p>Timing : 17.00Am - 20.00Pm</p></div>
  <div class="card" style="left:857px"><div class="photo" role="img" aria-label="Man lifting dumbbells" style="background:linear-gradient(135deg,#d2cfcb,#8a7f76)"></div><h4>Molestias Excepturi sint</h4><p>Timing : 17.00Am - 20.00Pm</p></div>
</section>

<section class="matching">
  <h2 class="title">Matching Client To Trainer</h2>
  <p class="intro">To take a trivial example, which of us ever undertakes laborious physical exercise, except to obtain some advantage</p>
  <div class="step" style="top:194px"><div class="play"><svg width="20" height="22"><path d="M2 1l17 10L2 21z" fill="#fff"/></svg></div><div class="txt"><h4>Nam libero tempore, cum soluta</h4><p>est eligendi optio cumque nihil impedit id ...</p></div></div>
  <div class="step" style="top:288px"><div class="play"><svg width="20" height="22"><path d="M2 1l17 10L2 21z" fill="#fff"/></svg></div><div class="txt"><h4>Nam libero tempore, cum soluta</h4><p>est eligendi optio cumque nihil impedit id ...</p></div></div>
  <div class="step" style="top:382px"><div class="play"><svg width="20" height="22"><path d="M2 1l17 10L2 21z" fill="#fff"/></svg></div><div class="txt"><h4>Nam libero tempore, cum soluta</h4><p>est eligendi optio cumque nihil impedit id ...</p></div></div>
  <div class="photo" role="img" aria-label="Group fitness class doing lunges in a studio" style="left:578px;top:85px;width:521px;height:310px;background:linear-gradient(120deg,#e9e4de,#c98a8a 50%,#6b5b55)"></div>
  <div class="caption"><div class="step play" style="position:static;width:66px;height:60px;background:var(--green);display:flex;align-items:center;justify-content:center"><svg width="20" height="22"><path d="M2 1l17 10L2 21z" fill="#fff"/></svg></div><div class="txt" style="padding:10px 14px"><h4>At vero eos et accusamus et iusto odio</h4><p>Ducimus qui blandiitis praesentium voluptatum deleniti atque...</p></div></div>
</section>

<section class="trainer">
  <h2 class="title abs" style="top:80px;width:100%">Our Trainer</h2>
  <div class="tbox"></div>
  <div class="avatar" role="img" aria-label="Portrait of the trainer"></div>
  <div class="stars">★★★★★</div>
  <p class="quote">At vero eos et accusamus et iusto odio dignissimos ducimus qui blandiitis praesentium voluptatum deleniti atque corrupti quos dolores et quas molestias excepturi sint occaecati cupiditate non provident, similique sunt in culpa qui officia deserunt.</p>
  <p class="tname">MARA LINTEL</p>
</section>

<section class="shop">
  <h2 class="title" style="left:100px">Fitness Products</h2>
  <h2 class="title" style="left:823px">FAQ</h2>
  <div class="product" style="left:100px"><div class="photo" role="img" aria-label="Supplement tub" style="background:linear-gradient(#eee,#3a3a3a 60%,#222)"></div><h5>PHYSICAL EXERCISE</h5><p class="desc">Lorem ipsum dolor sit amet,</p><div class="price">$ 99.9<span>★★★★</span></div><span class="buy">BUY NOW</span></div>
  <div class="product" style="left:327px"><div class="photo" role="img" aria-label="Shaker bottle and supplement containers" style="background:linear-gradient(#f4f4f4,#b33 70%,#444)"></div><h5>VOLUPTAS ASSUMENDA</h5><p class="desc">Lorem ipsum dolor sit amet,</p><div class="price">$ 99.9<span>★★★★</span></div><span class="buy">BUY NOW</span></div>
  <div class="product" style="left:553px"><div class="photo" role="img" aria-label="Protein powder bottles" style="background:linear-gradient(#6b4a3a,#1f2a4a 60%,#b03030)"></div><h5>TEMPORIBUS AUTEM</h5><p class="desc">Lorem ipsum dolor sit amet,</p><div class="price">$ 99.9<span>★★★★</span></div><span class="buy">BUY NOW</span></div>
  <ul class="faq">
    <li>What vero eos et accusamus?</li>
    <p class="answer">Those who do not know how to pursue pleasure rationally encounter consequences that are extremely painful.</p>
    <li>What pain can procure him some great ?</li>
    <li>What est eligendi optio cumque?</li>
    <li>What patterns are primarily focused on?</li>
    <li>What nihil impedit quo minus id ?</li>
    <li>What beguiled and demoralized charms?</li>
  </ul>
</section>

<section class="newsletter">
  <h2 class="title">News Letter Signin</h2>
  <p class="sub">Signup and see</p>
  <div class="nl-input">Enter the mail id</div>
  <div class="nl-btn">SUBSCRIBE</div>
</section>

<section class="contact">
  <h2 class="title abs" style="top:78px;width:100%">Contact Us</h2>
  <p class="intro">Ducimus qui blandiitis praesentium voluptatum deleniti atque corrupti quos dolores et quas molestias excepturi sint occaecati cupiditate non provident, similique sunt in culpa qui officia deserunt mollitia</p>
  <div class="field" style="left:100px;top:240px;width:321px;height:44px">Name</div>
  <div class="field" style="left:443px;top:240px;width:317px;height:44px">Name</div>
  <div class="field" style="left:779px;top:240px;width:320px;height:44px">Phone Number</div>
  <div class="field" style="left:100px;top:317px;width:647px;height:239px">Message</div>
  <div class="info" style="top:332px"><svg viewBox="0 0 18 18"><circle cx="9" cy="5" r="4" fill="#444"/><path d="M1 18a8 8 0 0 1 16 0z" fill="#444"/></svg>brisko.com</div>
  <div class="info" style="top:389px"><svg viewBox="0 0 18 18"><path d="M4 1l3 4-2 2a10 10 0 0 0 6 6l2-2 4 3-2 3C8 17 1 10 1 3z" fill="#444"/></svg>+1 555 0134 / 555 0178</div>
  <div class="info" style="top:442px"><svg viewBox="0 0 18 18"><rect x="1" y="4" width="16" height="11" fill="none" stroke="#444" stroke-width="2"/><path d="M1 4l8 6 8-6" fill="none" stroke="#444" stroke-width="2"/></svg>info@brisko.com</div>
  <div class="send">Contact Us</div>
</section>

<footer class="footer">
  <p class="copy">Copyright@Brisko2015 All Rights Reserved</p>
  <div class="social"><i style="background:#3b5998"></i><i style="background:#1da1f2"></i><i style="background:#dd4b39"></i><i style="background:#f39c12"></i></div>
  <span class="page">1/5</span>
</footer>

</body>
</html>
```